Fenwick Grading LTD - website for irrigation & Landscape Lighting & Buried service wire

Looking for a website to help promote my business with Irrigation (installation, service, etc) and buried service wire/drainage solutions.

Commercial/Residential

Landscape lighting.

I’ll get photos in the trucks and trailers to upload as well maybe the machine as well.

Target Market(s)

Homeowners who want green grass and beautiful gardens. Beautiful landscape lighting

Industry/Entity Type

Irrigation systems and landscape lighting and buried service wire to homes and offering Drainage soltions.

Coding

Coded - Design and coding required

Number of Pages Required

4 page

Colors
F0912C
F2A743
F7CA91
FBE8D2
FDF5EE

Requirements
Must have
• was hoping to link up my email on fenwickgrading@mailbox-example.net with the website if possible.
Nice to have
• Page for Irrigation, page for landscape lighting, page buried service wire & drainage soltions.

```html
<!DOCTYPE html>
<html lang="en">
<head>
<meta charset="utf-8">
<title>Fenwick Grading LTD</title>
<link href="https://fonts.googleapis.com/css2?family=Montserrat:wght@600;700;800&family=Roboto:wght@400;500;700&display=swap" rel="stylesheet">
<style>
:root{
  --orange:#F0912C;
  --orange-2:#F2A743;
  --orange-3:#F7CA91;
  --cream:#FBE8D2;
  --cream-2:#FDF5EE;
  --ink:#111111;
  --text:#333333;
  --muted:#777777;
  --grey-bg:#f4f4f4;
  --nav-bg:#efefef;
  --dark-btn:#6d6d6d;
  --white:#ffffff;
}
*{box-sizing:border-box;margin:0;padding:0}
html,body{width:1200px;height:3506px;overflow:hidden}
body{position:relative;background:var(--white);font-family:"Roboto",Arial,sans-serif;color:var(--text)}
.abs{position:absolute}
h1,h2,h3,.heading{font-family:"Montserrat",Arial,sans-serif}

/* header */
.contact-chip{position:absolute;display:flex;align-items:center;gap:12px}
.icon-circle{width:38px;height:38px;border-radius:50%;background:var(--orange);display:flex;align-items:center;justify-content:center;flex:none}
.icon-circle svg{width:18px;height:18px;fill:#fff}
.chip-label{font-family:"Montserrat",sans-serif;font-weight:700;font-size:14px;color:var(--orange);line-height:1.2}
.chip-value{font-size:17px;color:var(--ink);line-height:1.3}
.chip-value.bold{font-weight:700}
.brand{position:absolute;left:0;width:1200px;top:22px;text-align:center;display:flex;justify-content:center;align-items:center;gap:10px}
.brand-dot{width:14px;height:14px;background:var(--orange);border-radius:50%}
.brand-name{font-family:"Montserrat",sans-serif;font-weight:800;font-size:26px;color:var(--orange);line-height:1}

.nav{position:absolute;top:110px;left:0;width:1200px;height:55px;background:var(--nav-bg);clip-path:polygon(20px 0,100% 0,100% 100%,0 100%,0 20px)}
.nav-item{position:absolute;top:0;height:55px;line-height:58px;font-size:15px;color:var(--ink)}
.nav-home{position:absolute;top:105px;left:283px;width:65px;height:53px;background:var(--orange);border-radius:0 0 32px 32px;color:#fff;font-weight:700;font-size:15px;text-align:center;line-height:64px}

/* hero */
.hero-photo{position:absolute;top:165px;left:0;width:1200px;height:640px;background:radial-gradient(ellipse at 60% 45%,#4a3a1e 0%,#2a2612 35%,#121a0e 70%,#0b0f08 100%)}
.hero-glow{position:absolute;top:165px;left:0;width:1200px;height:640px;background:rgba(0,0,0,.25)}
.hero-welcome{position:absolute;top:345px;left:0;width:1200px;text-align:center;font-family:"Montserrat",sans-serif;font-weight:700;font-size:31px;color:var(--orange)}
.hero-title{position:absolute;top:388px;left:0;width:1200px;text-align:center;font-weight:800;font-size:62px;color:#fff;letter-spacing:.5px}
.hero-text{position:absolute;top:468px;left:380px;width:440px;text-align:center;font-size:15px;line-height:26px;color:#fff}
.btn{position:absolute;display:flex;align-items:center;justify-content:center;border-radius:27px;font-family:"Montserrat",sans-serif;font-weight:700;font-size:16px;color:#fff}
.btn-orange{background:var(--orange)}
.hero-btn{top:541px;left:517px;width:166px;height:54px}
.hero-edge{position:absolute;top:680px;left:0;width:1200px;height:125px}

/* services */
.section-title{position:absolute;left:0;width:1200px;text-align:center;font-weight:800;color:var(--ink)}
.service-card{position:absolute;top:967px;width:315px;height:336px;overflow:visible}
.service-photo{position:absolute;inset:0}
.service-shade{position:absolute;inset:0;background:linear-gradient(to bottom,rgba(0,0,0,0) 40%,rgba(0,0,0,.85) 85%)}
.service-title{position:absolute;left:21px;top:215px;width:294px;font-family:"Montserrat",sans-serif;font-weight:700;font-size:21px;line-height:35px;color:#fff;white-space:nowrap;letter-spacing:-.2px}
.service-text{position:absolute;left:22px;width:260px;font-size:15px;line-height:27px;color:#fff}
.round-btn{position:absolute;width:50px;height:50px;border-radius:50%;background:var(--orange);border:3px solid #fff;display:flex;align-items:center;justify-content:center}
.round-btn svg{width:18px;height:18px;stroke:#fff;fill:none;stroke-width:2.4;stroke-linecap:round;stroke-linejoin:round}
.slider-arrow{position:absolute;width:26px;height:26px;border-radius:50%;display:flex;align-items:center;justify-content:center}
.slider-arrow svg{width:10px;height:10px;fill:none;stroke-width:2;stroke-linecap:round;stroke-linejoin:round}
.arrow-on{background:var(--orange)}
.arrow-on svg{stroke:#fff}
.arrow-off{background:#eeeeee}
.arrow-off svg{stroke:#999}

/* about */
.about-bg{position:absolute;top:1420px;left:0;width:1200px;height:460px;background:var(--grey-bg)}
.about-heading{position:absolute;top:1496px;left:562px;font-weight:800;font-size:36px;color:#fff;white-space:nowrap}
.about-text{position:absolute;top:1557px;left:559px;width:535px;font-size:15px;line-height:26px;color:#fff}
.about-btn{top:1740px;left:559px;width:166px;height:53px;background:var(--dark-btn)}

/* testimonials */
.dot{position:absolute;border-radius:50%}
.avatar{position:absolute;border-radius:50%;background:linear-gradient(160deg,#c9c9c9,#7d7d7d)}
.t-name{position:absolute;top:2164px;left:0;width:1200px;text-align:center;font-family:"Montserrat",sans-serif;font-weight:700;font-size:19px;color:var(--ink)}
.t-role{position:absolute;top:2194px;left:0;width:1200px;text-align:center;font-size:15px;color:#444}
.stars{position:absolute;top:2225px;left:0;width:1200px;display:flex;justify-content:center;gap:4px}
.stars svg{width:16px;height:16px;fill:var(--orange)}
.t-text{position:absolute;top:2265px;left:280px;width:640px;text-align:center;font-size:15px;line-height:26px;color:var(--muted)}
.quote-mark{position:absolute;font-family:Georgia,serif;font-size:150px;color:#ececec;line-height:1}

/* contact */
.contact-bg{position:absolute;top:2467px;left:0;width:1200px;height:620px;background:var(--grey-bg)}
.info-row{position:absolute;left:98px;display:flex;gap:14px}
.info-icon{width:52px;height:52px;border-radius:50%;border:2px solid #bbb;display:flex;align-items:center;justify-content:center;flex:none;margin-top:-10px}
.info-icon svg{width:17px;height:17px;fill:var(--orange)}
.info-label{font-family:"Montserrat",sans-serif;font-weight:700;font-size:19px;color:var(--ink);line-height:1.2}
.info-value{font-size:15px;line-height:24px;color:#333;margin-top:4px}
.field{position:absolute;background:#fff;font-size:15px;color:#888;padding:0 24px;display:flex;align-items:center}
.field-msg{align-items:flex-start;padding-top:24px;box-shadow:0 6px 24px rgba(0,0,0,.05)}
.submit{position:absolute;top:2818px;left:422px;width:317px;height:53px;background:var(--orange);color:#fff;font-family:"Montserrat",sans-serif;font-weight:700;font-size:15px;display:flex;align-items:center;justify-content:center}

/* footer */
.footer-edge{position:absolute;top:2940px;left:0;width:1200px;height:141px}
.footer{position:absolute;top:3080px;left:0;width:1200px;height:426px;background:#000}
.footer-brand{position:absolute;top:3170px;left:130px;width:250px;text-align:center;font-family:"Montserrat",sans-serif;font-weight:800;font-size:30px;line-height:36px;color:var(--orange)}
.social{position:absolute;top:3295px;width:30px;height:30px;border-radius:50%;background:var(--orange)}
.social.alt{background:#fff}
.f-head{position:absolute;top:3140px;font-family:"Montserrat",sans-serif;font-weight:700;font-size:15px;color:#fff}
.f-rule{position:absolute;top:3167px;width:38px;height:3px;background:var(--orange)}
.f-links{position:absolute;top:3188px;list-style:none;font-size:15px;line-height:30px;color:#fff}
.f-text{position:absolute;top:3188px;left:802px;width:290px;font-size:15px;line-height:26px;color:#fff}
.f-input{position:absolute;top:3256px;left:801px;width:274px;height:42px;border-radius:21px;background:#fff;font-size:15px;color:#999;padding-left:20px;display:flex;align-items:center}
.f-send{position:absolute;top:3256px;left:1030px;width:45px;height:42px;border-radius:21px;background:var(--orange);display:flex;align-items:center;justify-content:center}
.f-send svg{width:18px;height:18px;fill:#fff}
.f-divider{position:absolute;top:3408px;left:112px;width:976px;height:1px;background:#2a2a2a}
.copyright{position:absolute;top:3443px;left:0;width:1200px;text-align:center;font-size:15px;color:#fff}
.copyright .accent{color:var(--orange)}
</style>
</head>
<body>

<!-- Header -->
<div class="contact-chip" style="left:115px;top:30px">
  <div class="icon-circle"><svg viewBox="0 0 24 24"><path d="M6.6 10.8a15.2 15.2 0 0 0 6.6 6.6l2.2-2.2c.3-.3.7-.4 1-.2 1.1.4 2.3.6 3.6.6.6 0 1 .4 1 1V20c0 .6-.4 1-1 1A17 17 0 0 1 3 4c0-.6.4-1 1-1h3.5c.6 0 1 .4 1 1 0 1.3.2 2.5.6 3.6.1.3 0 .7-.2 1z"/></svg></div>
  <div><div class="chip-label">CALL US</div><div class="chip-value bold">+1 888 888 8888</div></div>
</div>

<div class="brand"><span class="brand-dot"></span><span class="brand-name">FENWICK GRADING LTD</span></div>

<div class="contact-chip" style="left:804px;top:32px">
  <div class="icon-circle"><svg viewBox="0 0 24 24"><path d="M3 6h18v1.2l-9 6-9-6zM3 9.3l9 6 9-6V18H3z"/></svg></div>
  <div><div class="chip-label">EMAIL</div><div class="chip-value" style="font-size:16px">fenwickgrading@mailbox-example.net</div></div>
</div>

<nav class="nav">
  <span class="nav-item" style="left:378px">About Us</span>
  <span class="nav-item" style="left:482px">Irrigation</span>
  <span class="nav-item" style="left:586px">Landscape Lighting</span>
  <span class="nav-item" style="left:759px">Fiber Optic Installation</span>
</nav>
<div class="nav-home">Home</div>

<!-- Hero -->
<div class="hero-photo" role="img" aria-label="Garden path at dusk lit by lanterns among plants and flowers"></div>
<div class="hero-glow"></div>
<div class="hero-welcome">WELCOME TO</div>
<h1 class="hero-title">FENWICK GRADING</h1>
<p class="hero-text">Lorem ipsum dolor sit amet, consectetur adipiscing elit, sed do eiusmod tempor</p>
<div class="btn btn-orange hero-btn">GET STARTED</div>
<svg class="hero-edge" viewBox="0 0 1200 125" preserveAspectRatio="none">
  <path d="M0 8 L230 22 L575 100 L970 22 L1200 8 L1200 125 L0 125Z" fill="#F0912C"/>
  <path d="M0 22 L575 118 L1200 22 L1200 125 L0 125Z" fill="#ffffff"/>
</svg>

<!-- Services -->
<h2 class="section-title" style="top:887px;font-size:35px">OUR SERVICES</h2>

<div class="slider-arrow arrow-on" style="left:41px;top:1118px"><svg viewBox="0 0 10 10"><path d="M6.5 2 L3.5 5 L6.5 8"/></svg></div>
<div class="slider-arrow arrow-off" style="left:1131px;top:1118px"><svg viewBox="0 0 10 10"><path d="M3.5 2 L6.5 5 L3.5 8"/></svg></div>

<div class="service-card" style="left:110px">
  <div class="service-photo" role="img" aria-label="Lawn sprinkler watering a garden" style="background:linear-gradient(160deg,#6f8a4a,#34502a 55%,#1d2a16)"></div>
  <div class="service-shade"></div>
  <h3 class="service-title">IRRIGATION INSTALLS</h3>
  <p class="service-text" style="top:253px">Lorem ipsum dolor sit amet, con-sectetur adipiscing elit,</p>
  <div class="round-btn" style="left:255px;top:311px"><svg viewBox="0 0 20 20"><path d="M4 10h12M11 5l5 5-5 5"/></svg></div>
</div>

<div class="service-card" style="left:444px">
  <div class="service-photo" role="img" aria-label="Lit garden walkway in front of a house at night" style="background:linear-gradient(160deg,#5a6470,#2c3528 55%,#141a12)"></div>
  <div class="service-shade"></div>
  <h3 class="service-title">LANDSCAPE LIGHTING</h3>
  <p class="service-text" style="top:253px">Lorem ipsum dolor sit amet, con-sectetur adipiscing elit,</p>
  <div class="round-btn" style="left:255px;top:311px"><svg viewBox="0 0 20 20"><path d="M4 10h12M11 5l5 5-5 5"/></svg></div>
</div>

<div class="service-card" style="left:776px">
  <div class="service-photo" role="img" aria-label="Workers laying cable conduit in a dug trench" style="background:linear-gradient(160deg,#7b8aa0,#8a6a48 50%,#3a2a1c)"></div>
  <div class="service-shade"></div>
  <h3 class="service-title">FIBER OPTIC<br>INSTALLATION TO HOMES</h3>
  <p class="service-text" style="top:286px">Lorem ipsum dolor sit amet, con-</p>
  <div class="round-btn" style="left:255px;top:311px"><svg viewBox="0 0 20 20"><path d="M4 10h12M11 5l5 5-5 5"/></svg></div>
</div>

<!-- About -->
<div class="about-bg"></div>
<svg class="abs" style="top:1420px;left:0" width="1200" height="460" viewBox="0 0 1200 460">
  <path d="M567 0 L1200 0 L1200 455 L567 455 L395 267 Z" fill="#F0912C"/>
  <path d="M567 0 L1200 0 L1200 455 L567 455 L395 267 Z" fill="#F2A743" opacity=".35"/>
</svg>
<div class="abs" role="img" aria-label="Stone garden path lined with potted flowers" style="top:1479px;left:0;width:517px;height:400px;background:linear-gradient(150deg,#46602e,#6b6a4a 50%,#b7ae98);clip-path:polygon(0 0,327px 0,517px 208px,327px 400px,0 400px)"></div>
<h2 class="about-heading">ABOUT FENWICK GRADING</h2>
<p class="about-text">Lorem ipsum dolor sit amet, consectetur adipiscing elit, sed do eiusmod tempor incididunt ut labore et dolore magna aliqua. Quis ipsum suspendisse ultrices gravida. Risus commodo viverra maecenas accumsan lacus vel facilisis. Lorem ipsum dolor sit amet, consectetur adipiscing elit, sed do eiusmod tempor incididunt ut labore et dolore magna aliqua. Quis ipsum suspendisse ultrices gravida.</p>
<div class="btn about-btn">LEARN MORE</div>

<!-- Testimonials -->
<h2 class="section-title" style="top:1978px;font-size:35px">CLIENT TESTIMONIALS</h2>
<span class="dot" style="left:137px;top:2035px;width:7px;height:7px;background:#2aa3e0"></span>
<span class="dot" style="left:905px;top:1989px;width:9px;height:9px;background:var(--orange)"></span>
<span class="dot" style="left:322px;top:2139px;width:10px;height:10px;background:#f2c61f"></span>
<span class="dot" style="left:815px;top:2166px;width:10px;height:10px;background:#9b2fd6"></span>
<span class="dot" style="left:1015px;top:2335px;width:10px;height:10px;background:#2ed19b"></span>

<div class="avatar" role="img" aria-label="Client portrait" style="left:135px;top:2117px;width:48px;height:48px"></div>
<div class="avatar" role="img" aria-label="Client portrait" style="left:950px;top:2037px;width:48px;height:48px"></div>
<div class="avatar" role="img" aria-label="Portrait of the reviewing client" style="left:550px;top:2060px;width:90px;height:90px"></div>

<div class="slider-arrow arrow-off" style="left:206px;top:2168px;width:32px;height:32px"><svg viewBox="0 0 10 10"><path d="M6.5 2 L3.5 5 L6.5 8"/></svg></div>
<div class="slider-arrow arrow-on" style="left:960px;top:2168px;width:32px;height:32px"><svg viewBox="0 0 10 10"><path d="M3.5 2 L6.5 5 L3.5 8"/></svg></div>

<div class="t-name">Marlow Bennett</div>
<div class="t-role">Lorem Ipsum</div>
<div class="stars">
  <svg viewBox="0 0 20 20"><path d="M10 1l2.7 5.6 6.1.9-4.4 4.3 1 6.1L10 15l-5.4 2.9 1-6.1L1.2 7.5l6.1-.9z"/></svg>
  <svg viewBox="0 0 20 20"><path d="M10 1l2.7 5.6 6.1.9-4.4 4.3 1 6.1L10 15l-5.4 2.9 1-6.1L1.2 7.5l6.1-.9z"/></svg>
  <svg viewBox="0 0 20 20"><path d="M10 1l2.7 5.6 6.1.9-4.4 4.3 1 6.1L10 15l-5.4 2.9 1-6.1L1.2 7.5l6.1-.9z"/></svg>
  <svg viewBox="0 0 20 20"><path d="M10 1l2.7 5.6 6.1.9-4.4 4.3 1 6.1L10 15l-5.4 2.9 1-6.1L1.2 7.5l6.1-.9z"/></svg>
  <svg viewBox="0 0 20 20"><path d="M10 1l2.7 5.6 6.1.9-4.4 4.3 1 6.1L10 15l-5.4 2.9 1-6.1L1.2 7.5l6.1-.9z"/></svg>
</div>
<div class="quote-mark" style="left:245px;top:2180px">&ldquo;</div>
<p class="t-text">Lorem ipsum dolor sit amet, consectetur adipiscing elit, sed do eiusmod tempor incididunt ut labore et dolore magna aliqua. Quis ipsum suspendisse ultrices gravida. Risus commodo viverra maecenas accumsan lacus vel facilisis.</p>
<div class="quote-mark" style="left:880px;top:2320px">&rdquo;</div>

<!-- Contact -->
<div class="contact-bg"></div>
<h2 class="section-title" style="top:2530px;font-size:35px;left:-8px">CONTACT US</h2>

<div class="info-row" style="top:2622px">
  <div class="info-icon"><svg viewBox="0 0 24 24"><path d="M12 2a7 7 0 0 0-7 7c0 5 7 13 7 13s7-8 7-13a7 7 0 0 0-7-7zm0 9.5A2.5 2.5 0 1 1 12 6.5a2.5 2.5 0 0 1 0 5z"/></svg></div>
  <div><div class="info-label">LOCATION</div><div class="info-value">112/b Fenwick Grading sit amet,<br>consectetur adipiscing</div></div>
</div>
<div class="info-row" style="top:2734px">
  <div class="info-icon"><svg viewBox="0 0 24 24"><path d="M6.6 10.8a15.2 15.2 0 0 0 6.6 6.6l2.2-2.2c.3-.3.7-.4 1-.2 1.1.4 2.3.6 3.6.6.6 0 1 .4 1 1V20c0 .6-.4 1-1 1A17 17 0 0 1 3 4c0-.6.4-1 1-1h3.5c.6 0 1 .4 1 1 0 1.3.2 2.5.6 3.6.1.3 0 .7-.2 1z"/></svg></div>
  <div><div class="info-label">PHONE</div><div class="info-value">+1 888 888 8888</div></div>
</div>
<div class="info-row" style="top:2824px">
  <div class="info-icon"><svg viewBox="0 0 24 24"><path d="M3 6h18v1.2l-9 6-9-6zM3 9.3l9 6 9-6V18H3z"/></svg></div>
  <div><div class="info-label">EMAIL</div><div class="info-value" style="font-size:14px">fenwickgrading@mailbox-example.net</div></div>
</div>

<div class="field" style="top:2612px;left:422px;width:317px;height:53px">Name</div>
<div class="field" style="top:2680px;left:422px;width:317px;height:53px">Phone</div>
<div class="field" style="top:2748px;left:422px;width:317px;height:53px">Email</div>
<div class="submit">SUBMIT</div>
<div class="field field-msg" style="top:2612px;left:759px;width:317px;height:259px">Type your message</div>

<!-- Footer -->
<svg class="footer-edge" viewBox="0 0 1200 141" preserveAspectRatio="none">
  <path d="M0 100 L575 12 L1200 100 L1200 141 L0 141Z" fill="#F0912C"/>
  <path d="M0 118 L575 52 L1040 118 L1200 118 L1200 141 L0 141Z" fill="#000000"/>
</svg>
<footer class="footer"></footer>

<div class="footer-brand">FENWICK<br>GRADING LTD</div>
<span class="social" style="left:178px" aria-label="Social link"></span>
<span class="social alt" style="left:218px" aria-label="Social link"></span>
<span class="social alt" style="left:257px" aria-label="Social link"></span>
<span class="social alt" style="left:295px" aria-label="Social link"></span>

<div class="f-head" style="left:415px">QUICK LINKS</div>
<span class="f-rule" style="left:415px"></span>
<ul class="f-links" style="left:417px">
  <li>Home</li><li>About Us</li><li>Irrigation</li><li>Landscape Lighting</li><li>Fiber Optic Installation</li>
</ul>

<div class="f-head" style="left:627px">SUPPORT</div>
<span class="f-rule" style="left:627px"></span>
<ul class="f-links" style="left:630px">
  <li>Terms &amp; Conditions</li><li>Privacy Policy</li><li>About Us</li><li>Support</li>
</ul>

<div class="f-head" style="left:800px">SUBSCRIBE TO OUR NEWSLETTER</div>
<span class="f-rule" style="left:800px"></span>
<p class="f-text">Lorem ipsum dolor sit amet, consectetur adipiscing elit, sed do</p>
<div class="f-input">Enter Your Email</div>
<div class="f-send"><svg viewBox="0 0 24 24"><path d="M21 3 3 10.5l6.5 2.5L18 6l-7 8.5V21l3.5-4.5 4 2.5z"/></svg></div>

<div class="f-divider"></div>
<p class="copyright">©Copyrights 2024 &nbsp;<span class="accent">Fenwick Grading</span> &nbsp;| &nbsp; All Rights Reserved</p>

</body>
</html>
```